BUSINESS CARD FOR GUITAR SCHOOL

I would like to design a business card for my Guitar Music School. The school is called "Pluck & Lantern".

The card should be yellow.

Target Market(s)

18-35 years old

Industry/Entity Type

School

Contact Information for Business Card

I would like to design a business card for my Guitar Music School. The school is called "Pluck & Lantern". The card should be yellow.

Card must be consistent with my website design: www.pluckandlantern.com.sg

Requirements
Must have
• 1) Name of Company
• 2) Company Logo
• 3) Name of Employee
• 4) Position of Employee
• 5) Contact Number
• 6) Address
Nice to have
• Creative Design
• Card must be consistent with my website design: www.pluckandlantern.com.sg
Should not have
• Boring Design

```html
<!DOCTYPE html>
<html lang="en">
<head>
<meta charset="utf-8">
<title>Pluck &amp; Lantern — Business Card</title>
<link rel="stylesheet" href="https://fonts.googleapis.com/css2?family=Open+Sans:wght@400;600;800&display=swap">
<style>
  :root {
    --yellow: #f8d40c;
    --yellow-deep: #f2c200;
    --ink: #111111;
    --paper: #ffffff;
    --text-grey: #333333;
    --backdrop: #e9e6e1;
  }
  * { box-sizing: border-box; margin: 0; padding: 0; }
  html, body {
    width: 1200px; height: 913px; overflow: hidden;
    background: var(--backdrop);
    font-family: "Open Sans", Arial, sans-serif;
  }
  .stage { position: relative; width: 1200px; height: 913px; }

  .card {
    position: absolute;
    width: 520px; height: 300px;
    border-radius: 4px;
    overflow: hidden;
    box-shadow: 0 10px 30px rgba(0,0,0,0.18);
  }

  /* Front */
  .card--front {
    left: 70px; top: 100px;
    background: linear-gradient(135deg, var(--yellow) 0%, var(--yellow-deep) 100%);
  }
  .front-brand {
    position: absolute; left: 0; right: 0; top: 0; bottom: 0;
    display: flex; align-items: center; justify-content: center; gap: 14px;
  }
  .brand-dot {
    width: 22px; height: 22px; border-radius: 50%;
    background: var(--ink);
  }
  .brand-name {
    font-weight: 800; color: var(--ink);
    letter-spacing: -0.5px;
  }
  .front-brand .brand-name { font-size: 44px; }

  /* Back */
  .card--back {
    left: 610px; top: 470px;
    background: var(--paper);
  }
  .back-band { position: absolute; left: 0; top: 0; width: 520px; height: 300px; }
  .back-brand {
    position: absolute; left: 30px; top: 34px;
    display: flex; align-items: center; gap: 8px;
  }
  .back-brand .brand-dot { width: 12px; height: 12px; }
  .back-brand .brand-name { font-size: 22px; }

  .person { position: absolute; left: 30px; top: 96px; }
  .person-name { font-weight: 800; font-size: 17px; color: var(--ink); }
  .person-role { font-weight: 600; font-size: 11.5px; color: var(--text-grey); margin-top: 2px; }

  .address {
    position: absolute; left: 30px; top: 150px;
    font-size: 11px; line-height: 1.45; color: var(--text-grey);
  }
  .contacts {
    position: absolute; left: 30px; top: 194px;
    list-style: none; font-size: 11px; color: var(--text-grey);
  }
  .contacts li { display: flex; align-items: center; gap: 8px; height: 18px; }
  .contacts li.web { font-weight: 600; color: var(--ink); }
  .contact-icon { width: 11px; height: 11px; fill: var(--yellow-deep); flex: none; }
</style>
</head>
<body>
<main class="stage">

  <section class="card card--front" aria-label="Business card front">
    <div class="front-brand">
      <span class="brand-dot"></span>
      <span class="brand-name">Pluck &amp; Lantern</span>
    </div>
  </section>

  <section class="card card--back" aria-label="Business card back">
    <svg class="back-band" viewBox="0 0 520 300" aria-hidden="true">
      <polygon points="150,300 520,300 520,222" fill="var(--yellow)"/>
      <polygon points="470,300 520,300 520,222 490,228" fill="var(--ink)"/>
    </svg>

    <div class="back-brand">
      <span class="brand-dot"></span>
      <span class="brand-name">Pluck &amp; Lantern</span>
    </div>

    <div class="person">
      <p class="person-name">Your Long Name</p>
      <p class="person-role">Managing Director</p>
    </div>

    <p class="address">27 Keris Lane Harbour Building<br>B #05-03 Singapore 418822</p>

    <ul class="contacts">
      <li>
        <svg class="contact-icon" viewBox="0 0 24 24"><path d="M6.6 10.8a15 15 0 0 0 6.6 6.6l2.2-2.2a1 1 0 0 1 1-.25 11.4 11.4 0 0 0 3.6.57 1 1 0 0 1 1 1V20a1 1 0 0 1-1 1A17 17 0 0 1 3 4a1 1 0 0 1 1-1h3.5a1 1 0 0 1 1 1c0 1.25.2 2.45.57 3.6a1 1 0 0 1-.25 1z"/></svg>
        +65 91234567
      </li>
      <li>
        <svg class="contact-icon" viewBox="0 0 24 24"><path d="M2 5h20v14H2z M2 5l10 8 10-8" /></svg>
        yourname@pluckandlantern.com.sg
      </li>
      <li class="web">
        <svg class="contact-icon" viewBox="0 0 24 24"><circle cx="12" cy="12" r="10"/></svg>
        www.pluckandlantern.com.sg
      </li>
    </ul>
  </section>

</main>
</body>
</html>
```